Private label Bottled water label design

We are launching private label water bottle case packs with our brand “tallyway”
Need bottle labels design as well as case pack design artwork. Bottle is 16.9oz similar to pet brovani quellin bottles.
It will be spring water.
Case pack will be of 24 bottles
Tallyway is a chain of convenience stores in Texas
www.tallywaymarkets.example
I have attached pictures of brovani water. It would be similar packaging for single and case pack.

Target Market(s)

Male female shoppers middle aged. Take home package or single serve in cold vault

Industry/Entity Type

Water bottle retail

Colors
0054AA
0677BA
7BADD7
CADEEF
E8F1F8
59FF00
82FF00
B8FF75
E3FFCB
F4FFEA

Requirements
Must have
• Very premium look. Use the logo of tallyway
Nice to have
• Elegant premium water look
Should not have
• I am open to all

```html
<!DOCTYPE html>
<html lang="en">
<head>
<meta charset="utf-8">
<title>Tallyway Mountain Spring Water – Bottle Label</title>
<link rel="stylesheet" href="https://fonts.googleapis.com/css2?family=DM+Sans:wght@400;500;800&display=swap">
<style>
  :root {
    --backdrop: #c6e2df;
    --label-white: #ffffff;
    --pattern-tone: #f3f4f3;
    --band-black: #1b1b1b;
    --accent-green: #8fd400;
    --accent-green-light: #b8ff75;
    --ink-dark: #222222;
    --text-light: #ffffff;
  }
  html, body {
    margin: 0;
    padding: 0;
    width: 934px;
    height: 1200px;
    overflow: hidden;
    background: var(--backdrop);
  }
  .canvas {
    position: relative;
    width: 934px;
    height: 1200px;
  }
  .bottle-label {
    position: absolute;
    left: 21px;
    top: 248px;
    width: 891px;
    height: 704px;
    background: var(--pattern-tone);
    overflow: hidden;
    font-family: "DM Sans", sans-serif;
  }
  .label-art {
    position: absolute;
    inset: 0;
  }
  .brand-name {
    position: absolute;
    left: 0;
    right: 0;
    top: 148px;
    text-align: center;
    font-family: "DM Sans", sans-serif;
    font-weight: 800;
    font-size: 140px;
    line-height: 1;
    letter-spacing: -4px;
    color: var(--ink-dark);
  }
  .net-volume {
    position: absolute;
    left: 56px;
    top: 600px;
    font-size: 22px;
    font-weight: 500;
    color: var(--accent-green);
  }
  .product-name {
    position: absolute;
    left: 0;
    right: 0;
    top: 588px;
    text-align: center;
    font-size: 30px;
    font-weight: 500;
    line-height: 1.2;
    color: var(--text-light);
  }
  .natural-badge {
    position: absolute;
    left: 772px;
    top: 580px;
    width: 72px;
    text-align: center;
  }
  .natural-icon {
    display: block;
    margin: 0 auto;
  }
  .natural-badge span {
    display: block;
    margin-top: 4px;
    font-size: 12px;
    letter-spacing: 1px;
    color: var(--accent-green);
  }
</style>
</head>
<body>
<div class="canvas">
  <div class="bottle-label">
    <svg class="label-art" width="891" height="704" viewBox="0 0 891 704">
      <rect class="pattern-field" x="0" y="0" width="891" height="704" fill="var(--pattern-tone)" role="img" aria-label="Faint grey chevron line pattern behind the brand name"/>
      <polygon class="mountain-band" points="0,355 125,432 279,377 455,509 686,377 807,432 891,355 891,704 0,704" fill="var(--band-black)"/>
      <polyline class="mountain-ridge-light" points="0,352 125,429 279,374 455,506 686,374 807,429 891,352" fill="none" stroke="var(--accent-green-light)" stroke-width="6" stroke-linejoin="miter"/>
      <polyline class="mountain-ridge" points="0,341 125,418 279,363 455,495 686,363 807,418 891,341" fill="none" stroke="var(--accent-green)" stroke-width="12" stroke-linejoin="miter"/>
    </svg>

    <div class="brand-name">tallyway</div>

    <div class="net-volume">16,9 oz</div>
    <div class="product-name">Mountain Spring<br>Water</div>

    <div class="natural-badge">
      <svg class="natural-icon" width="34" height="46" viewBox="0 0 34 46">
        <path d="M17 3 C17 3 4 20 4 30 A13 13 0 0 0 30 30 C30 20 17 3 17 3 Z" fill="none" stroke="var(--accent-green)" stroke-width="2"/>
        <path d="M17 38 L17 22 M17 30 L11 24 M17 27 L22 22" fill="none" stroke="var(--accent-green)" stroke-width="1.6" stroke-linecap="round"/>
      </svg>
      <span>NATURAL</span>
    </div>
  </div>
</div>
</body>
</html>
```